Maple n Brook - Contact/Landing Page

I need a landing page which will essentially be the page that customers will go to from the 'website' link on QTV listing. It will provide a short overview of services which need to be selectable. a little further down can capture some contact details followed by a large Submit Now button etc...

I have some icon/logo's that can be utilised at the bottom of the page as industry type references.

Target Market(s)

End of Lease Cleaning Services

Industry/Entity Type

Cleaning Service

Colors

Designer to choose colors to be used in the design.

Requirements
Must have
• As per description
Should not have
• Colours to match my website maplenbrook.com.au

```html
<!DOCTYPE html>
<html lang="en">
<head>
<meta charset="utf-8">
<title>Maple n Brook – End of Lease Cleaning</title>
<link href="https://fonts.googleapis.com/css2?family=Fira+Sans:wght@400;600;700&family=Open+Sans:wght@400;600&display=swap" rel="stylesheet">
<style>
  :root {
    --brand-blue: #1f74be;
    --icon-blue: #2486cf;
    --ink: #111111;
    --charcoal: #1d1d1d;
    --white: #ffffff;
    --field-text: #333333;
    --muted: #8a8a8a;
    --border: #c9c9c9;
  }
  * { margin: 0; padding: 0; box-sizing: border-box; }
  html, body { width: 1200px; height: 2274px; overflow: hidden; background: var(--white); }
  .page { position: relative; width: 1200px; height: 2274px; overflow: hidden; font-family: "Open Sans", sans-serif; color: var(--ink); }

  .hero { position: absolute; left: 0; top: 0; width: 1200px; height: 640px; background: var(--brand-blue); }
  .hero-edge { position: absolute; left: 0; top: 540px; width: 1200px; height: 100px; }
  .brand { position: absolute; left: 0; top: 190px; width: 1200px; display: flex; justify-content: center; align-items: center; gap: 14px; }
  .brand-dot { width: 34px; height: 34px; border-radius: 50%; background: var(--white); }
  .brand-name { font-family: "Fira Sans", sans-serif; font-weight: 700; font-size: 44px; color: var(--white); }
  .hero-title { position: absolute; left: 0; top: 352px; width: 1200px; text-align: center; font-family: "Fira Sans", sans-serif; font-weight: 700; font-size: 41px; color: var(--white); }
  .hero-sub { position: absolute; left: 0; top: 406px; width: 1200px; text-align: center; font-family: "Fira Sans", sans-serif; font-size: 24px; color: var(--white); letter-spacing: 0.3px; }

  .service { position: absolute; top: 725px; width: 290px; text-align: center; }
  .service-icon { width: 120px; height: 120px; margin: 0 auto; border-radius: 50%; background: var(--icon-blue); display: flex; align-items: center; justify-content: center; }
  .service-title { margin-top: 10px; font-family: "Fira Sans", sans-serif; font-size: 34px; line-height: 44px; }
  .service-text { margin-top: 6px; font-size: 13px; line-height: 24px; height: 48px; }
  .select-btn { margin: 18px auto 0; width: 128px; height: 48px; border: 1px solid #9a9a9a; display: flex; align-items: center; justify-content: center; gap: 14px; font-family: "Fira Sans", sans-serif; font-size: 19px; }
  .check { width: 15px; height: 15px; border: 1px solid #777; border-radius: 3px; display: flex; align-items: center; justify-content: center; }
  .check.on { border-color: var(--icon-blue); }
  .check.on::after { content: ""; width: 7px; height: 7px; border-radius: 50%; background: var(--icon-blue); }

  .contact-band { position: absolute; left: 0; top: 1100px; width: 1200px; height: 740px; }
  .enquiry-form { position: absolute; left: 144px; top: 1239px; width: 336px; }
  .field { height: 53px; background: var(--white); margin-bottom: 11px; padding-left: 14px; display: flex; align-items: center; font-size: 16px; color: var(--field-text); }
  .submit-panel { margin-top: 0; height: 141px; background: var(--icon-blue); padding-top: 14px; text-align: center; }
  .submit-email { font-size: 21px; color: var(--white); line-height: 28px; }
  .submit-btn { margin: 16px auto 0; width: 314px; height: 70px; border: 2px solid var(--white); border-radius: 3px; display: flex; align-items: center; justify-content: center; font-size: 39px; color: var(--white); letter-spacing: 1px; }

  .accreditations { position: absolute; left: 144px; top: 1932px; display: flex; gap: 7px; }
  .accreditation { width: 177px; height: 95px; border: 1px solid var(--border); display: flex; align-items: center; justify-content: center; }
  .accreditation span { display: block; width: 100px; height: 40px; border-radius: 3px; background: #d7dde6; }

  .footer-band { position: absolute; left: 0; top: 2110px; width: 1200px; height: 164px; }
  .copyright { position: absolute; left: 144px; top: 2210px; font-size: 11.5px; color: var(--muted); }
  .social-dot { position: absolute; left: 1040px; top: 2207px; width: 18px; height: 18px; border-radius: 50%; background: var(--muted); }
</style>
</head>
<body>
<div class="page">
  <header class="hero">
    <div class="brand"><span class="brand-dot"></span><span class="brand-name">Maple n Brook</span></div>
    <h1 class="hero-title">END OF LEASE CLEANING</h1>
    <p class="hero-sub">Licensed Pest Control</p>
    <svg class="hero-edge" viewBox="0 540 1200 100" width="1200" height="100">
      <polygon points="600,582 1200,550 1200,614" fill="var(--charcoal)"/>
      <polygon points="0,613 600,582 1200,614 1200,640 0,640" fill="var(--white)"/>
    </svg>
  </header>

  <section class="services">
    <div class="service" style="left:141px">
      <div class="service-icon">
        <svg width="64" height="64" viewBox="0 0 64 64" fill="none" stroke="#fff" stroke-width="2">
          <rect x="6" y="8" width="20" height="14"/><circle cx="36" cy="14" r="5"/>
          <rect x="32" y="24" width="8" height="10"/><line x1="50" y1="14" x2="50" y2="54"/>
          <rect x="6" y="38" width="38" height="12" rx="2"/><line x1="8" y1="50" x2="8" y2="55"/><line x1="42" y1="50" x2="42" y2="55"/>
        </svg>
      </div>
      <h2 class="service-title">Cleaning</h2>
      <p class="service-text">All interior cleaning carried out to property management requirements</p>
      <div class="select-btn">SELECT <span class="check on"></span></div>
    </div>
    <div class="service" style="left:455px">
      <div class="service-icon">
        <svg width="64" height="64" viewBox="0 0 64 64" fill="none" stroke="#fff" stroke-width="2">
          <rect x="18" y="8" width="28" height="48"/><rect x="24" y="16" width="16" height="32"/>
          <circle cx="32" cy="32" r="5"/>
        </svg>
      </div>
      <h2 class="service-title">Carpet Cleaning</h2>
      <p class="service-text">Carpet steam cleaning to Australian standard as 3733: 1995</p>
      <div class="select-btn">SELECT <span class="check"></span></div>
    </div>
    <div class="service" style="left:769px">
      <div class="service-icon">
        <svg width="64" height="64" viewBox="0 0 64 64" fill="none" stroke="#fff" stroke-width="2.5">
          <circle cx="32" cy="32" r="27"/><line x1="13" y1="13" x2="51" y2="51"/>
        </svg>
      </div>
      <h2 class="service-title">Pest Control</h2>
      <p class="service-text">Mandatory requirement for pets on premises</p>
      <div class="select-btn">SELECT <span class="check"></span></div>
    </div>
  </section>

  <svg class="contact-band" viewBox="0 1100 1200 740" width="1200" height="740" role="img" aria-label="Photo of a technician in a white protective suit spraying pest treatment beside a dark metal wall">
    <defs>
      <linearGradient id="photoTone" x1="0" y1="0" x2="1" y2="0">
        <stop offset="0" stop-color="#000000"/>
        <stop offset="0.45" stop-color="#0b1122"/>
        <stop offset="0.75" stop-color="#2d3a66"/>
        <stop offset="1" stop-color="#4a5688"/>
      </linearGradient>
    </defs>
    <polygon points="0,1164 1200,1103 1200,1773 0,1835" fill="url(#photoTone)"/>
  </svg>

  <form class="enquiry-form">
    <div class="field">First Name</div>
    <div class="field">Surname</div>
    <div class="field">Email</div>
    <div class="field">Phone</div>
    <div class="field">Suburb</div>
    <div class="submit-panel">
      <div class="submit-email">info@maplenbrook.com.au</div>
      <div class="submit-btn">SUBMIT</div>
    </div>
  </form>

  <section class="accreditations" aria-label="Industry accreditations">
    <div class="accreditation"><span></span></div>
    <div class="accreditation"><span></span></div>
    <div class="accreditation"><span></span></div>
    <div class="accreditation"><span></span></div>
    <div class="accreditation"><span></span></div>
  </section>

  <svg class="footer-band" viewBox="0 2110 1200 164" width="1200" height="164">
    <polygon points="0,2177 1200,2114 1200,2274 0,2274" fill="var(--charcoal)"/>
  </svg>
  <p class="copyright">Copyright &nbsp;©&nbsp; 2021 &nbsp;Maple n Brook. &nbsp;&nbsp;All rights reserved.</p>
  <span class="social-dot"></span>
</div>
</body>
</html>
```